sydney wedding photography business needs a business card design

we need a business card design for a sydney based wedding photography and videography business. our business name is :golden hour studio and film. our target clients are 24-35 yrs female. our style is candid, organic, natural, dynamic. we are a team of young photographers and videographers, and help brides to create memories that they will cherish for the rest of their lives. the logo will be provided. we want an elegant design that reflects our style, and also want to give a great impression to our clients that we are one of the best studios in sydney and our brand means quality and premium service.

Target Market(s)

bride to be, 24-35 years old, living in sydney and surrunding areas

Industry/Entity Type

Wedding Photography

Contact Information for Business Card

address: 57 tarrant street, glenmore nsw 2047
mobile: 0431872259
phone: (02) 9163 2408
info@tidewillowstudio.net.au
www.tidewillowstudio.net.au
facebook:tidewillowweddings
instagram:tidewillowweddings

Font styles to use
Serif
Sans Serif

Requirements
Nice to have
• maybe add my slogan"memories beyond eternity" if the layout looks good
Should not have
• no black color, not good idea for wedding biz card

```html
<!DOCTYPE html>
<html lang="en">
<head>
<meta charset="utf-8">
<title>Golden Hour Studio and Film – Business Card</title>
<link rel="stylesheet" href="https://fonts.googleapis.com/css2?family=Questrial&display=swap">
<style>
  :root {
    --backdrop: #ebe5da;
    --gold-light: #dba815;
    --gold-mid: #c08f16;
    --gold-deep: #a0701c;
    --espresso: #2a1f16;
    --espresso-deep: #1f1710;
    --ink-soft: #2a1f16;
    --paper-text: #ece4d6;
    --shadow: rgba(60, 40, 10, 0.28);
  }
  * { box-sizing: border-box; margin: 0; padding: 0; }
  html, body {
    width: 1200px;
    height: 774px;
    overflow: hidden;
    background: var(--backdrop);
    font-family: "Questrial", "Century Gothic", sans-serif;
  }
  .stage {
    position: relative;
    width: 1200px;
    height: 774px;
    display: flex;
    align-items: center;
    justify-content: center;
    gap: 60px;
  }
  .card {
    position: relative;
    width: 520px;
    height: 297px;
    border-radius: 3px;
    box-shadow: 0 10px 24px var(--shadow);
    overflow: hidden;
  }

  /* Front face */
  .card-front {
    background: radial-gradient(ellipse at 50% 40%, var(--gold-light) 0%, var(--gold-mid) 45%, var(--gold-deep) 100%);
    display: flex;
    flex-direction: column;
    align-items: center;
    justify-content: center;
  }
  .front-name {
    color: var(--ink-soft);
    font-size: 28px;
    letter-spacing: 0.06em;
    text-transform: uppercase;
    text-align: center;
    line-height: 1.25;
    margin-top: -20px;
  }
  .social-handle {
    position: absolute;
    bottom: 48px;
    left: 0;
    right: 0;
    display: flex;
    align-items: center;
    justify-content: center;
    gap: 8px;
    color: var(--ink-soft);
    font-size: 15px;
  }
  .social-dot {
    width: 14px;
    height: 14px;
    border-radius: 50%;
    background: var(--ink-soft);
  }

  /* Back face */
  .card-back {
    background: linear-gradient(160deg, var(--espresso) 0%, var(--espresso-deep) 100%);
  }
  .gold-tab {
    position: absolute;
    background: linear-gradient(180deg, var(--gold-light), var(--gold-deep));
  }
  .gold-tab-right {
    right: 0;
    top: 30px;
    width: 10px;
    height: 62px;
    border-radius: 8px 0 0 8px;
  }
  .gold-tab-left {
    left: 0;
    bottom: 18px;
    width: 12px;
    height: 62px;
    border-radius: 0 8px 8px 0;
  }
  .wordmark {
    position: absolute;
    top: 76px;
    left: 60px;
    right: 60px;
    text-align: center;
    color: var(--gold-light);
    font-size: 22px;
    font-weight: 400;
    letter-spacing: 0.08em;
    text-transform: uppercase;
    white-space: nowrap;
  }
  .contact-block {
    position: absolute;
    top: 140px;
    right: 34px;
    text-align: right;
    color: var(--paper-text);
    font-size: 13px;
    line-height: 1.45;
    text-transform: uppercase;
  }
  .contact-label {
    color: var(--gold-light);
  }
  .person-block {
    position: absolute;
    left: 34px;
    bottom: 26px;
    color: var(--paper-text);
    font-size: 13px;
    line-height: 1.45;
    text-transform: uppercase;
  }
  .person-name {
    color: var(--gold-light);
    font-size: 17px;
  }
</style>
</head>
<body>
  <main class="stage">
    <section class="card card-front" aria-label="Card front">
      <p class="front-name">Golden Hour<br>Studio and Film</p>
      <p class="social-handle"><span class="social-dot"></span>tidewillowweddings</p>
    </section>

    <section class="card card-back" aria-label="Card back">
      <span class="gold-tab gold-tab-right"></span>
      <span class="gold-tab gold-tab-left"></span>
      <h1 class="wordmark">Golden Hour Studio and Film</h1>

      <div class="contact-block">
        <p><span class="contact-label">Phone :</span> (02) 9163 2408</p>
        <p><span class="contact-label">Cell :</span> 0431 872 259</p>
        <p>info@tidewillowstudio.net.au</p>
        <p>www.tidewillowstudio.net.au</p>
      </div>

      <div class="person-block">
        <p class="person-name">Maya Lindqvist</p>
        <p>CEO/Founder</p>
        <p>57 Tarrant Street</p>
        <p>Glenmore NSW 2047</p>
      </div>
    </section>
  </main>
</body>
</html>
```